Emergency Management Consulting Needs a Website

Need to develop a website for an Emergency Management Consulting business. This website needs to be user friendly and resemble disaster preparedness, response, recovery, and mitigation. It must allow for me to make changes to it myself by adding pages, content and pictures. Looking for an advanced page to the website that allows monitoring of social media sites, hashtags, and keywords. Must have pictures of disasters on the site. Must try to integrate the logo colors, not excessive.

Reason: Did not receive anything sufficient to what I am looking for.

Industry/Entity Type

Government

Coding

Coded - Design and coding required

Number of Pages Required

5+ page

Requirements
Must have
• Logo, advanced social media monitoring page, allow for edits myself (content, pages, graphics) this must be a CMS of some sort, use logo color scheme (not excessively), must be professional looking, connect with Plivex Domain, find a hosting site, SEO, no "long" designs, minimize "dead" space, no social media feeds, no newsletter stuff.
• Menu items: Home, About Us, Services, Situation Monitor, Work With Us, Contact Us (hopefully these could be editable if I need to later)
• When you make a submission, please send me a message on which CMS you are using. Thank you.
Nice to have
• Examples of websites:
• https://www.qrt.vic.gov.au/
• http://www.larkenmoss.example/
• http://www.tulpaxo.example/
• http://vonmirelconsulting.example/
• http://www.calvornet.example/services/emergency-management
• https://zuq.example/
• http://www.vestimora.example/Responsibility/Sustainable-Development/HSE/Crisis-and-Emergency-Management/

```html
<!DOCTYPE html>
<html lang="en">
<head>
<meta charset="utf-8">
<title>Marlow Bend Emergency Management</title>
<link rel="stylesheet" href="https://fonts.googleapis.com/css2?family=Arimo:ital,wght@0,400;0,700;1,400&family=Exo+2:wght@300;400;600;700&family=Roboto+Condensed:wght@300;400&display=swap">
<style>
:root{
  --blue:#1b9ad9;
  --blue-dark:#1a3e98;
  --navy:#0f2450;
  --ink:#222;
  --muted:#777;
  --grey-band:#ececec;
  --footer:#232323;
  --white:#fff;
  --accent:#f28c1e;
}
*{margin:0;padding:0;box-sizing:border-box}
html,body{width:1200px;height:3797px;overflow:hidden;background:var(--white)}
body{font-family:"Arimo",Arial,sans-serif;color:var(--ink);position:relative}
a{text-decoration:none}
.abs{position:absolute}
.heading{font-family:"Exo 2",Arial,sans-serif;font-weight:400;text-transform:uppercase}
.heading b{font-weight:600;color:var(--blue)}

/* header */
.site-header{position:absolute;left:0;top:0;width:1200px;height:127px;background:var(--white);border-top:6px solid var(--blue)}
.brand{left:76px;top:32px;display:flex;align-items:center;gap:14px}
.brand-dot{width:58px;height:58px;border-radius:50%;background:var(--blue)}
.brand-name{font-family:"Exo 2",sans-serif;font-weight:700;font-size:36px;line-height:38px;color:#333;letter-spacing:1px;white-space:nowrap}
.brand-sub{font-family:"Exo 2",sans-serif;font-weight:600;font-size:13px;color:#333;letter-spacing:3px;line-height:18px;white-space:nowrap}
.call{right:70px;top:20px;display:flex;align-items:center;gap:12px;font-size:15px;white-space:nowrap}
.call .num{font-size:20px}
.phone-ring{width:42px;height:42px;border:2px solid var(--blue);border-radius:50%;display:flex;align-items:center;justify-content:center}
.main-nav{right:70px;top:66px;display:flex;align-items:center;gap:18px;font-size:14px;white-space:nowrap}
.main-nav a{color:#555;text-transform:uppercase}
.main-nav a.active{background:var(--blue);color:var(--white);padding:13px 24px;border-radius:2px}

/* hero */
.hero{left:0;top:127px;width:1200px;height:557px;background:linear-gradient(180deg,#3b4650 0%,#5d6a72 45%,#7d8a80 72%,#4e5a3c 100%)}
.hero-title{left:516px;top:150px;font-family:"Roboto Condensed",sans-serif;font-weight:300;font-size:76px;color:var(--white);letter-spacing:1px;line-height:1;white-space:nowrap}
.hero-text{left:521px;top:252px;width:610px;font-size:17px;line-height:29px;color:var(--white)}
.btn-outline{display:inline-block;border:2px solid var(--white);border-radius:6px;color:var(--white);text-transform:uppercase;font-size:19px;text-align:center}
.hero .btn-outline{position:absolute;left:527px;top:334px;width:187px;height:61px;line-height:57px;background:var(--blue)}
.hero-arrow{top:265px;width:52px;height:52px;border:2px solid rgba(255,255,255,.8);border-radius:50%;display:flex;align-items:center;justify-content:center}

/* intro band */
.intro{left:0;top:684px;width:1200px;height:341px;background:linear-gradient(90deg,#1b9ad9 0%,#1a67b8 55%,#1a3e98 100%);text-align:center;color:var(--white)}
.intro-mark{left:572px;top:34px;width:56px;height:56px;border-radius:50%;background:var(--accent)}
.intro-title{position:absolute;left:0;top:118px;width:1200px;font-size:40px;font-weight:600;color:var(--white)}
.intro-title span{font-weight:300;color:var(--navy)}
.intro-text{position:absolute;left:125px;top:186px;width:950px;font-size:13.5px;line-height:26px}
.intro-chev{left:586px;top:276px}

/* services */
.services{left:0;top:1025px;width:1200px;height:494px;text-align:center}
.section-title{position:absolute;left:0;width:1200px;font-size:42px;color:#222}
.section-sub{position:absolute;left:0;width:1200px;font-size:15px;color:#555;text-transform:uppercase}
.service{top:172px;width:260px;text-align:center}
.service-icon{width:126px;height:126px;margin:0 auto;border-radius:50%;background:var(--blue);display:flex;align-items:center;justify-content:center;box-shadow:0 14px 12px -10px rgba(0,0,0,.25)}
.service-icon .ring{width:104px;height:104px;border:3px solid var(--white);border-radius:50%;display:flex;align-items:center;justify-content:center}
.service h3{font-weight:400;font-size:17px;text-transform:uppercase;margin-top:38px;color:#333}
.service p{font-size:13.5px;line-height:26px;color:var(--muted);margin-top:10px}

/* welcome */
.welcome{left:0;top:1519px;width:1200px;height:426px;background:linear-gradient(90deg,#1b9ad9 0%,#1a6cbb 50%,#1a3e98 100%);color:var(--white)}
.welcome-title{left:81px;top:62px;font-size:40px;color:var(--white);white-space:nowrap}
.welcome-title span{color:var(--navy);font-weight:400}
.welcome-title b{color:var(--white)}
.welcome-sub{left:81px;top:120px;font-size:15px;text-transform:uppercase}
.welcome-text{left:81px;top:150px;width:730px;font-size:14px;line-height:26px}
.welcome-text p+p{margin-top:10px}
.welcome .btn-outline{position:absolute;left:81px;top:306px;width:170px;height:56px;line-height:52px;font-size:18px}
.welcome-mark{left:850px;top:180px;display:flex;align-items:center;gap:16px}
.welcome-mark .dot{width:64px;height:64px;border-radius:50%;background:var(--accent)}
.welcome-mark .name{font-family:"Exo 2",sans-serif;font-weight:700;font-size:32px;color:var(--white);white-space:nowrap}

/* testimonial */
.testimonial{left:0;top:1945px;width:1200px;height:313px;background:var(--grey-band)}
.avatar{left:141px;top:62px;width:188px;height:188px;border-radius:50%;border:6px solid var(--white);background:radial-gradient(circle at 50% 40%,#c9b6a6 0%,#8c8fa0 60%,#6d7488 100%);box-shadow:0 10px 12px rgba(0,0,0,.2)}
.testimonial-title{left:357px;top:60px;font-size:40px;color:#222;white-space:nowrap}
.quote{left:357px;top:135px;width:740px;font-size:15px;line-height:26px;font-style:italic;color:#666}
.client-name{left:365px;top:224px;font-size:15px;font-weight:700;color:var(--blue);text-transform:uppercase;display:flex;align-items:center;gap:14px}
.client-name::before{content:"";width:26px;height:3px;background:var(--blue)}
.t-arrow{top:140px}

/* projects */
.projects{left:0;top:2258px;width:1200px;height:965px;text-align:center}
.tile{width:324px;height:317px}
.tile-feature{background:var(--blue);color:var(--white);display:flex;flex-direction:column;align-items:center;padding-top:82px}
.tile-feature h3{font-family:"Exo 2",sans-serif;font-weight:400;font-size:30px;text-transform:uppercase}
.tile-feature p{width:240px;font-size:14px;line-height:26px;margin-top:18px}
.btn-solid{left:522px;top:849px;width:156px;height:56px;line-height:56px;background:var(--blue);color:var(--white);border-radius:5px;font-size:18px;text-transform:uppercase}

/* news */
.news{left:0;top:3223px;width:1200px;height:228px;background:var(--grey-band)}
.news-item{top:61px;display:flex;gap:20px;width:320px}
.date{width:63px;flex:none;text-align:center;color:var(--white)}
.date .day{background:#1e5fae;font-family:"Exo 2",sans-serif;font-size:38px;height:68px;line-height:68px;font-weight:600}
.date .month{background:#111;font-size:15px;height:41px;line-height:41px}
.news-item h4{font-size:15px;line-height:22px;font-weight:700;color:#111}
.news-item p{font-size:13px;line-height:21px;color:#444;margin-top:6px}
.news-item a{display:block;font-size:13px;color:var(--blue);text-decoration:underline;margin-top:4px}

/* footer */
.site-footer{left:0;top:3451px;width:1200px;height:279px;background:var(--footer);color:#bbb}
.f-col{top:48px}
.f-col h5{font-size:18px;font-weight:700;color:var(--blue);text-transform:uppercase;margin-bottom:14px}
.f-col li{list-style:none;font-size:14px;line-height:27px;display:flex;align-items:center;gap:12px;white-space:nowrap}
.f-col li::before{content:"";width:7px;height:7px;border-right:2px solid var(--blue);border-top:2px solid var(--blue);transform:rotate(45deg)}
.contact-row{display:flex;gap:16px;font-size:14px;line-height:21px;margin-bottom:12px}
.contact-row svg{flex:none;margin-top:2px}
.f-mark{left:950px;top:52px;display:flex;flex-direction:column;align-items:center;gap:10px;width:164px}
.f-mark .dot{width:54px;height:54px;border-radius:50%;background:var(--accent)}
.f-mark .name{font-family:"Exo 2",sans-serif;font-weight:700;font-size:22px;color:var(--white);white-space:nowrap}
.social{left:942px;top:192px;display:flex;gap:7px}
.social span{width:46px;height:46px;border-radius:50%;border:2px solid #888}
.social span.on{background:var(--blue);border-color:var(--blue)}
.copyright{left:0;top:3730px;width:1200px;height:67px;background:var(--blue);color:var(--white);font-size:15px;text-align:center;line-height:67px}
.copyright b{font-weight:700}
</style>
</head>
<body>

<header class="site-header">
  <div class="brand abs">
    <span class="brand-dot"></span>
    <div>
      <div class="brand-name">MARLOW BEND</div>
      <div class="brand-sub">EMERGENCY MANAGEMENT</div>
    </div>
  </div>
  <div class="call abs">
    <span>Call Us On :</span>
    <span class="phone-ring"><svg width="20" height="20" viewBox="0 0 24 24"><path d="M6.6 10.8a15 15 0 0 0 6.6 6.6l2.2-2.2c.3-.3.7-.4 1-.2 1.1.4 2.3.6 3.6.6.6 0 1 .4 1 1V20c0 .6-.4 1-1 1A17 17 0 0 1 3 4c0-.6.4-1 1-1h3.5c.6 0 1 .4 1 1 0 1.3.2 2.5.6 3.6.1.3 0 .7-.2 1z" fill="#1b9ad9"/></svg></span>
    <span class="num">123 456 7890</span>
  </div>
  <nav class="main-nav abs">
    <a class="active" href="#">Home</a>
    <a href="#">About Us</a>
    <a href="#">Services</a>
    <a href="#">Situation Monitor</a>
    <a href="#">Work With Us</a>
    <a href="#">Contact Us</a>
  </nav>
</header>

<section class="hero abs" role="img" aria-label="Photo of a tornado touching down over open plains under dark storm clouds">
  <span class="hero-arrow abs" style="left:16px"><svg width="16" height="16" viewBox="0 0 16 16"><path d="M10 2 4 8l6 6" fill="none" stroke="#fff" stroke-width="2"/></svg></span>
  <span class="hero-arrow abs" style="left:1136px"><svg width="16" height="16" viewBox="0 0 16 16"><path d="m6 2 6 6-6 6" fill="none" stroke="#fff" stroke-width="2"/></svg></span>
  <h1 class="hero-title abs">DISASTER RECOVERY</h1>
  <p class="hero-text abs">Lorem Ipsum is simply dummy text of the printing and type setting the is industry. Lorem Ipsum has been the industry's standard .</p>
  <a class="btn-outline" href="#">Contact Now</a>
</section>

<section class="intro abs">
  <span class="intro-mark abs"></span>
  <h2 class="intro-title heading"><span>Marlow Bend</span> Emergency Management</h2>
  <p class="intro-text">Lorem Ipsum is simply dummy text of the printing and typesetting industry. Lorem Ipsum has been the industry's standard dummy text ever since the 1500s, when an unknown printer took a galley of type and scrembled it to make a type specimen book. It has survived not only five centuries, but also the leap into electronic k a galley of type and scrambled it to make a type specimen.</p>
  <svg class="intro-chev abs" width="28" height="24" viewBox="0 0 28 24"><path d="m7 3 7 7 7-7M7 12l7 7 7-7" fill="none" stroke="#fff" stroke-width="2.5"/></svg>
</section>

<section class="services abs">
  <h2 class="section-title heading" style="top:60px">Our Best <b>Services</b></h2>
  <p class="section-sub" style="top:122px">What we do</p>

  <div class="service abs" style="left:70px">
    <div class="service-icon"><div class="ring"><svg width="60" height="56" viewBox="0 0 60 56"><path d="M30 4 4 26h8v26h36V26h8L30 4z" fill="#fff"/><rect x="24" y="34" width="12" height="18" fill="#1b9ad9"/><rect x="16" y="28" width="8" height="8" fill="#1b9ad9"/><rect x="36" y="28" width="8" height="8" fill="#1b9ad9"/></svg></div></div>
    <h3>Disaster Preparedness</h3>
    <p>Lorem Ipsum is simply dummy text of the printing and typesetting industry. Lorem Ipsum text.</p>
  </div>
  <div class="service abs" style="left:338px">
    <div class="service-icon"><div class="ring"><svg width="56" height="56" viewBox="0 0 56 56"><rect x="6" y="24" width="10" height="26" fill="#fff"/><path d="M20 24 30 6c4 0 6 3 5 7l-2 9h14c3 0 5 3 4 6l-5 18c-1 3-3 4-6 4H20z" fill="#fff"/></svg></div></div>
    <h3>Response</h3>
    <p>Lorem Ipsum is simply dummy text of the printing and typesetting industry. Lorem Ipsum text.</p>
  </div>
  <div class="service abs" style="left:602px">
    <div class="service-icon"><div class="ring"><svg width="58" height="58" viewBox="0 0 58 58"><circle cx="29" cy="29" r="25" fill="none" stroke="#fff" stroke-width="5"/><path d="M24 14h10v10h10v10H34v10H24V34H14V24h10z" fill="#fff"/></svg></div></div>
    <h3>Recovery</h3>
    <p>Lorem Ipsum is simply dummy text of the printing and typesetting industry. Lorem Ipsum text.</p>
  </div>
  <div class="service abs" style="left:870px">
    <div class="service-icon"><div class="ring"><svg width="60" height="56" viewBox="0 0 60 56"><path d="M26 4 2 48h34" fill="none" stroke="#fff" stroke-width="5" stroke-linejoin="round"/><path d="M26 4 44 36" fill="none" stroke="#fff" stroke-width="5"/><rect x="23.5" y="18" width="5" height="16" fill="#fff"/><rect x="23.5" y="38" width="5" height="5" fill="#fff"/><circle cx="46" cy="42" r="12" fill="#fff"/><path d="m40 42 4 4 8-8" fill="none" stroke="#1b9ad9" stroke-width="3"/></svg></div></div>
    <h3>Mitigation</h3>
    <p>Lorem Ipsum is simply dummy text of the printing and typesetting industry. Lorem Ipsum text.</p>
  </div>
</section>

<section class="welcome abs">
  <h2 class="welcome-title heading abs"><span>Welcome to</span> <b>Marlow Bend</b></h2>
  <p class="welcome-sub abs">Emergency Management</p>
  <div class="welcome-text abs">
    <p>Lorem Ipsum is simply dummy text of the printing and typesetting industry. Lorem Ipsum has been the industry's standard dummy text ever since the 1500s, when an unknown printer took a galley of.</p>
    <p>Lorem Ipsum is simply dummy text of the printing and typesetting industry. Lorem Ipsum has been the industry's standard dummy text ever since the 1500s, when an unknown printer took a galley of type and scrambled it to make a type specimen book. It has survived not only five centuries, but also the leap into electronic.</p>
  </div>
  <a class="btn-outline" href="#">Know More</a>
  <div class="welcome-mark abs"><span class="dot"></span><span class="name">MARLOW BEND</span></div>
</section>

<section class="testimonial abs">
  <svg class="t-arrow abs" style="left:78px" width="18" height="34" viewBox="0 0 18 34"><path d="M16 2 3 17l13 15" fill="none" stroke="#aaa" stroke-width="2"/></svg>
  <svg class="t-arrow abs" style="left:1104px" width="18" height="34" viewBox="0 0 18 34"><path d="m2 2 13 15L2 32" fill="none" stroke="#aaa" stroke-width="2"/></svg>
  <div class="avatar abs" role="img" aria-label="Portrait photo of the client"></div>
  <h2 class="testimonial-title heading abs">What our <b>Client Say</b></h2>
  <p class="quote abs">Lorem Ipsum is simply dummy text of the printing and typesetting industry. Lorem Ipsum has been the industry's standard dummy text ever since the 1500s, when an unknown printer took a galley of type and scrambled it to make a type specimen book.</p>
  <p class="client-name abs">Client Name</p>
</section>

<section class="projects abs">
  <h2 class="section-title heading" style="top:56px">Latest <b>Projects</b></h2>
  <p class="section-sub" style="top:118px">Our work</p>
  <div class="tile abs" style="left:94px;top:180px;background:linear-gradient(160deg,#6f7f92,#3e4c60 60%,#2a3344)" role="img" aria-label="Photo of a smoke-filled street after a disaster"></div>
  <div class="tile tile-feature abs" style="left:438px;top:180px">
    <h3>Project Title</h3>
    <p>Lorem Ipsum is simply dummy text of the printing and typesetting industry. Lorem Ipsum has been the industry's standard dummy he industry's .</p>
  </div>
  <div class="tile abs" style="left:780px;top:180px;background:linear-gradient(170deg,#5a5f5e,#3c4343 55%,#6f6a55)" role="img" aria-label="Photo of a rescue worker in a yellow raincoat on a flooded street"></div>
  <div class="tile abs" style="left:94px;top:512px;background:linear-gradient(160deg,#d98a3c,#7a3d1e 50%,#2b2520)" role="img" aria-label="Photo of firefighters facing a burning building"></div>
  <div class="tile abs" style="left:438px;top:512px;background:linear-gradient(170deg,#c9a25a,#6a4d2e 55%,#2f2722)" role="img" aria-label="Photo of police lined up on a city street at night"></div>
  <div class="tile abs" style="left:780px;top:512px;background:linear-gradient(165deg,#9aa3ad,#b5582c 50%,#6a2e1c)" role="img" aria-label="Photo of a large brick building on fire with fire crews below"></div>
  <a class="btn-solid abs" href="#">View All</a>
</section>

<section class="news abs">
  <article class="news-item abs" style="left:94px">
    <div class="date"><div class="day">16</div><div class="month">March</div></div>
    <div><h4>Lorem Ipsum is the simply text of the printing.</h4><p>Lorem Ipsum is simply dummy text of the printing &amp; type.</p><a href="#">READ MORE</a></div>
  </article>
  <article class="news-item abs" style="left:446px">
    <div class="date"><div class="day">15</div><div class="month">March</div></div>
    <div><h4>Lorem Ipsum is the simply text of the printing.</h4><p>Lorem Ipsum is simply dummy text of the printing &amp; type.</p><a href="#">READ MORE</a></div>
  </article>
  <article class="news-item abs" style="left:810px">
    <div class="date"><div class="day">14</div><div class="month">March</div></div>
    <div><h4>Lorem Ipsum is the simply text of the printing.</h4><p>Lorem Ipsum is simply dummy text of the printing &amp; type.</p><a href="#">READ MORE</a></div>
  </article>
</section>

<footer class="site-footer abs">
  <div class="f-col abs" style="left:81px">
    <h5>Usefull Links</h5>
    <ul><li>Home</li><li>About Us</li><li>Services</li><li>Situation Monitor</li><li>Work With Us</li><li>Contact Us</li></ul>
  </div>
  <div class="f-col abs" style="left:344px">
    <h5>Services</h5>
    <ul><li>Disaster Preparedness</li><li>Response</li><li>Recovery</li><li>Mitigation</li></ul>
  </div>
  <div class="f-col abs" style="left:610px;width:300px">
    <h5>Contact</h5>
    <div class="contact-row"><svg width="20" height="28" viewBox="0 0 20 28"><path d="M10 0C4.5 0 0 4.4 0 9.8 0 17 10 28 10 28s10-11 10-18.2C20 4.4 15.5 0 10 0zm0 14a4 4 0 1 1 0-8 4 4 0 0 1 0 8z" fill="#1b9ad9"/></svg><span>MARLOW BEND<br>101 - Lorem ipsum is simple dummy text of print and type setting text of print.</span></div>
    <div class="contact-row"><svg width="20" height="20" viewBox="0 0 24 24"><path d="M6.6 10.8a15 15 0 0 0 6.6 6.6l2.2-2.2c.3-.3.7-.4 1-.2 1.1.4 2.3.6 3.6.6.6 0 1 .4 1 1V20c0 .6-.4 1-1 1A17 17 0 0 1 3 4c0-.6.4-1 1-1h3.5c.6 0 1 .4 1 1 0 1.3.2 2.5.6 3.6.1.3 0 .7-.2 1z" fill="#1b9ad9"/></svg><span>123 456 7890</span></div>
    <div class="contact-row"><svg width="20" height="16" viewBox="0 0 20 16"><rect width="20" height="16" rx="2" fill="#1b9ad9"/><path d="m1 2 9 7 9-7" fill="none" stroke="#232323" stroke-width="2"/></svg><span>info@MarlowBend.example</span></div>
  </div>
  <div class="f-mark abs"><span class="dot"></span><span class="name">MARLOW BEND</span></div>
  <div class="social abs"><span class="on"></span><span></span><span></span></div>
</footer>

<div class="copyright abs">© <b>MARLOW BEND EMERGENCY MANAGEMENT</b> - 2017 . All Rights Reserved</div>

</body>
</html>
```